elegant beautiful Hang tag for a novelty makeup towel

It's a black hand towel in the shape of a little black dress. it is called PETAL CHARM TOWEL, it is a CLEAN SLATE MAKEUP TOWEL. (doesn't show our makeup stains) Made in USA

Target Market(s)

ALL Women , Makeup artists, novelty THIS WILL BE IN THE HALVERGATE STORES AND KESTRELMOOR STORES.

Industry/Entity Type

Makeup

Contact Information for Business Card

I actually need a hang tag for a homemade handmade towel. I have a logo that I want on the tag and know what we want to say on it, on back needs to say "The essential to every girl's wardrobe. So when the little black dress comes off, our PETAL CHARM TOWEL is there to help you wash your day away. Include website www.petalcharmtowel.com OH INCLUDE TM (trademark sign next to logo please. Also, in small print on back from the makers of THE ORIGINAL CLEAN SLATE MAKEUP TOWEL. handmade in USA. also CLEAN SLATE MAKEUP TOWEL IN big font on front under logo sign with light colored pink lips after 'CLEAN SLATE" but have no idea about fonts, graphics, placement or design. Want it classy, elegant, girly! COLORS LIGHT BEIGER BACKGROUND WITH BLACK WRITING/ DESIGNS

Font styles to use
Serif
Decorative
Script

Colors
fff3d1

Requirements
Must have
• Black cream girly , also state in big writing that it's a " clean slate makeup towel" with a tiny light pink lip between the show and makeup. Include www.petalcharmtowel.com Brightwater Fenn, LLC
Nice to have
• Perhaps an outline of a little black dress. A black scroll edge of some sort around card. Classy

```html
<!DOCTYPE html>
<html lang="en">
<head>
<meta charset="UTF-8">
<title>Petal Charm Towel – Cards</title>
<link href="https://fonts.googleapis.com/css2?family=Cormorant+Garamond:wght@500;600&family=Montserrat:wght@400;500;600&display=swap" rel="stylesheet">
<style>
  :root {
    --ink: #0d0d0d;
    --cream: #fff3d1;
    --blush: #f08a8f;
    --lip: #f6bcc4;
    --stage: #2b2b2b;
    --rule: #555555;
  }
  * { box-sizing: border-box; margin: 0; padding: 0; }
  html, body { width: 1200px; height: 900px; overflow: hidden; }
  body {
    background: var(--stage);
    font-family: "Montserrat", Arial, sans-serif;
    position: relative;
  }
  .card {
    position: absolute;
    width: 640px;
    height: 366px;
    background: var(--cream);
    border-radius: 22px;
    overflow: hidden;
    color: var(--ink);
  }
  .card .wave { position: absolute; inset: 0; width: 100%; height: 100%; }
  .card-front { left: 60px; top: 50px; }
  .card-back { left: 500px; top: 484px; }

  /* front */
  .front-brand {
    position: absolute;
    right: 50px;
    top: 46px;
    width: 320px;
    text-align: center;
  }
  .front-name {
    font-size: 26px;
    font-weight: 600;
    letter-spacing: 3px;
    line-height: 1.25;
  }
  .tm { font-size: 12px; vertical-align: super; letter-spacing: 0; margin-left: 2px; }
  .front-tagline {
    margin-top: 12px;
    font-family: "Cormorant Garamond", Georgia, serif;
    font-size: 25px;
    font-weight: 600;
    letter-spacing: 2px;
    line-height: 1.2;
  }
  .lips { display: inline-block; width: 30px; height: 14px; vertical-align: middle; margin: 0 4px; }
  .front-url {
    position: absolute;
    left: 36px;
    bottom: 28px;
    color: var(--cream);
    font-size: 19px;
    letter-spacing: 0.5px;
  }
  .small-print {
    position: absolute;
    right: 30px;
    bottom: 26px;
    width: 230px;
    text-align: right;
    color: var(--cream);
    font-size: 9.5px;
    letter-spacing: 0.6px;
    line-height: 1.5;
  }

  /* back */
  .brand-block { position: absolute; left: 40px; top: 40px; width: 300px; }
  .brand-name {
    font-size: 22px;
    font-weight: 500;
    letter-spacing: 3px;
    border-bottom: 1px solid var(--rule);
    padding-bottom: 4px;
  }
  .brand-tagline {
    margin-top: 4px;
    font-size: 10px;
    letter-spacing: 1.5px;
    color: var(--blush);
    text-align: center;
  }
  .person { position: absolute; right: 34px; top: 46px; width: 240px; text-align: right; }
  .person-name {
    font-size: 23px;
    font-weight: 600;
    color: var(--blush);
    border-bottom: 1px solid var(--rule);
    padding-bottom: 2px;
  }
  .person-role { font-size: 13px; margin-top: 2px; }

  .story {
    position: absolute;
    left: 40px;
    top: 124px;
    width: 560px;
    font-family: "Cormorant Garamond", Georgia, serif;
    font-size: 15px;
    font-weight: 500;
    line-height: 1.3;
  }
  .contact {
    position: absolute;
    left: 40px;
    top: 200px;
    width: 250px;
    border-top: 1px solid var(--rule);
    padding-top: 8px;
    font-size: 14px;
    line-height: 1.35;
  }
  .contact-line { display: flex; align-items: center; gap: 8px; }
  .contact-line svg { width: 13px; height: 13px; flex: none; }
  .company { font-weight: 600; }
</style>
</head>
<body>

<section class="card card-front">
  <svg class="wave" viewBox="0 0 640 366" preserveAspectRatio="none" aria-hidden="true">
    <path d="M0,262 C150,300 300,320 430,250 C530,196 600,180 640,170 L640,366 L0,366 Z" fill="var(--blush)"/>
    <path d="M0,276 C150,312 300,332 430,264 C530,212 600,198 640,190 L640,366 L0,366 Z" fill="var(--ink)"/>
  </svg>
  <div class="front-brand">
    <div class="front-name">PETAL CHARM TOWEL<span class="tm">™</span></div>
    <div class="front-tagline">
      CLEAN SLATE<svg class="lips" viewBox="0 0 30 14" role="img" aria-label="Light pink lips"><ellipse cx="15" cy="7" rx="14" ry="6" fill="var(--lip)"/></svg><br>MAKEUP TOWEL
    </div>
  </div>
  <div class="front-url">www.petalcharmtowel.com</div>
  <div class="small-print">From the makers of THE ORIGINAL CLEAN SLATE MAKEUP TOWEL<br>Handmade in USA</div>
</section>

<section class="card card-back">
  <svg class="wave" viewBox="0 0 640 366" preserveAspectRatio="none" aria-hidden="true">
    <path d="M0,356 C180,370 360,330 470,260 C550,210 600,196 640,190 L640,366 L0,366 Z" fill="var(--blush)"/>
    <path d="M120,366 C300,360 420,310 500,262 C570,222 610,212 640,208 L640,366 Z" fill="var(--ink)"/>
  </svg>

  <div class="brand-block">
    <div class="brand-name">PETAL CHARM TOWEL<span class="tm">™</span></div>
    <div class="brand-tagline">CLEAN SLATE MAKEUP TOWEL</div>
  </div>

  <div class="person">
    <div class="person-name">Maren Ellsworth</div>
    <div class="person-role">Director</div>
  </div>

  <p class="story">The essential to every girl's wardrobe. So when the little black dress comes off, our PETAL CHARM TOWEL is there to help you wash your day away.</p>

  <div class="contact">
    <div class="company">Brightwater Fenn, LLC</div>
    <div>48 Copperfield Lane, Ashbury, NY 10000</div>
    <div class="contact-line">
      <svg viewBox="0 0 16 16"><path d="M3 1l3 3-2 2c1 2 3 4 5 5l2-2 3 3-2 3C7 15 1 9 1 3z" fill="var(--blush)"/></svg>
      +330 5182-0947
    </div>
    <div class="contact-line">
      <svg viewBox="0 0 16 16"><rect x="1" y="3" width="14" height="10" fill="none" stroke="var(--blush)" stroke-width="1.6"/><path d="M1 3l7 6 7-6" fill="none" stroke="var(--blush)" stroke-width="1.6"/></svg>
      info@petalcharmtowel.com
    </div>
    <div class="contact-line">
      <svg viewBox="0 0 16 16"><circle cx="8" cy="8" r="6.5" fill="none" stroke="var(--blush)" stroke-width="1.4"/><path d="M1.5 8h13M8 1.5c-3 3.5-3 9.5 0 13M8 1.5c3 3.5 3 9.5 0 13" fill="none" stroke="var(--blush)" stroke-width="1.2"/></svg>
      www.petalcharmtowel.com
    </div>
  </div>
</section>

</body>
</html>
```